Simple, 1-Page Project - Life-saving Harborlane Devices

We recently kicked off a project to bring all geographic location records for automatic emergency defibrillators (AEDs) in the State of New York online (instead of kept in paper in drawers). This hope is that is will ultimately save thousands of lives, as 9-1-1 operators will be able to quickly direct civilians to the nearest AED to bring to people suffering a cardiac event (e.g., a heart attack).

This page will be used to describe this effort, our progress thus far and how far we have left to go.

I am looking for a 1-page design - coded for both a responsive version for mobile devices and a traditional version - that would ***ideally*** plug into my existing WordPress site (https://qv-lmt.org), but it's not a requirement.

Target Market(s)

General public (non-physicians/non-EMTs)

Requirements
Must have
• - Our logo (please note, our logo is the Birchfield Vale Chapter logo...attached)
Nice to have
• - Would be wonderful to have an area with a clickable map showing where the participating regions are - which, once clicked, will take to you their specific sites. Regions are large chunks of land encompassing multiple towns, NOT a singular, specific place A nice-looking Google Map, a la Plumtail Grids (https://plumtailgrids.com/) would be cool if this were possible..
• - If you need a headline or page title, you can use: "Bringing AEDs in New York Online"
• - Would be nice if the design incorporated the color scheme of our brand (see attachment) and/or our main website: https://qv-lmt.org/
• - Would be nice to have some AED imagery - I attached some common symbols seen in AED advertising for inspiration
Should not have
• - This is a serious topic, so the design should be respectful and not too silly/cartoonish
• - Stock images, if chosen, should be thoughtful and classy

```html
<!DOCTYPE html>
<html lang="en">
<head>
<meta charset="utf-8">
<title>Bringing AEDs in New York Online</title>
<link rel="stylesheet" href="https://fonts.googleapis.com/css2?family=Roboto:wght@400;500;700&family=Jost:wght@400;500&display=swap">
<style>
:root{
  --navy:#0b2e5e;
  --navy-deep:#082448;
  --olive:#a3a07c;
  --olive-btn:#a7a57a;
  --ink:#1c1c1c;
  --body:#6b6b6b;
  --line:#c9cdd6;
  --card-line:#7b90b2;
  --footer:#2b2b2b;
  --white:#ffffff;
  --star:#e5c300;
}
*{box-sizing:border-box;margin:0;padding:0}
html,body{width:1200px;height:3852px;overflow:hidden}
body{position:relative;background:var(--white);font-family:"Jost",sans-serif;color:var(--body)}
.abs{position:absolute}

/* header */
.site-header{position:absolute;left:0;top:0;width:1200px;height:105px;background:var(--white)}
.brand{position:absolute;left:112px;top:24px;display:flex;align-items:center;gap:12px}
.brand-mark{width:56px;height:56px;border-radius:50%;background:var(--ink)}
.brand-name{font-family:"Jost",sans-serif;font-size:16px;line-height:16px;color:var(--ink);letter-spacing:.5px;text-transform:uppercase}
.phone{position:absolute;left:596px;top:21px;display:flex;align-items:center;gap:14px}
.phone-icon{width:36px;height:36px;border:1px solid var(--line);border-radius:50%;display:flex;align-items:center;justify-content:center}
.phone-num{font-family:"Roboto",sans-serif;font-size:20px;font-weight:500;color:var(--navy)}
.search{position:absolute;left:826px;top:25px;width:260px;height:31px;border:1px solid #aaa;border-radius:3px;font-size:13px;color:#999;padding:7px 12px}
.search svg{position:absolute;right:14px;top:8px}
.main-nav{position:absolute;top:77px;left:482px;font-family:"Roboto",sans-serif;font-size:14px;font-weight:500;color:var(--ink)}
.main-nav a{color:inherit;text-decoration:none;position:absolute;white-space:nowrap}
.main-nav a.active{color:var(--navy);border-bottom:2px solid var(--navy);padding-bottom:5px}

/* hero */
.hero{position:absolute;left:0;top:105px;width:1200px;height:624px;background:linear-gradient(115deg,#5a5f66 0%,#3e4f68 35%,#6d6a66 60%,#8f857d 100%)}
.hero-title{position:absolute;left:108px;top:98px;font-family:"Roboto",sans-serif;font-weight:500;font-size:48px;line-height:64px;color:var(--white)}
.hero-text{position:absolute;left:112px;top:250px;width:500px;font-size:16px;line-height:27px;color:var(--white)}
.btn-quote{position:absolute;left:112px;top:332px;width:136px;height:40px;background:var(--olive-btn);color:var(--white);font-family:"Roboto",sans-serif;font-weight:500;font-size:15px;display:flex;align-items:center;justify-content:center}
.hero-dots{position:absolute;left:583px;top:545px;display:flex;gap:5px}
.hero-dots span{width:9px;height:9px;border:1.5px solid var(--white);border-radius:50%}
.hero-dots span.on{background:var(--white)}

/* section titles */
.section-title{position:absolute;left:0;width:1200px;text-align:center;font-family:"Roboto",sans-serif;font-weight:500;font-size:36px;color:var(--ink);text-transform:uppercase}
.section-lead{position:absolute;left:0;width:1200px;text-align:center;font-size:16px;line-height:27px;color:var(--body)}

/* service cards */
.service-card{position:absolute;top:1020px;width:237px;height:243px;border:1.5px solid var(--card-line);text-align:center}
.service-icon{position:absolute;left:50%;top:-50px;margin-left:-46px;width:92px;height:92px;border-radius:50%;border:1.5px solid var(--card-line);background:var(--white);display:flex;align-items:center;justify-content:center}
.service-card h3{position:absolute;top:63px;left:0;width:100%;font-family:"Roboto",sans-serif;font-weight:500;font-size:16px;color:var(--ink)}
.service-card p{position:absolute;top:98px;left:0;width:100%;font-size:15px;line-height:27px;color:var(--body)}
.read-more{position:absolute;top:193px;left:0;width:100%;font-family:"Roboto",sans-serif;font-weight:500;font-size:15px;color:var(--navy)}

/* about band */
.about-band{position:absolute;left:0;top:1357px;width:1200px;height:438px;background:var(--navy)}
.about-art{position:absolute;left:157px;top:87px;width:337px;height:269px;border-radius:6px;background:linear-gradient(90deg,#e9762c 0%,#e9762c 55%,#6c9b61 56%,#6c9b61 100%)}
.about-title{position:absolute;left:561px;top:78px;font-family:"Roboto",sans-serif;font-weight:500;font-size:37px;line-height:48px;color:var(--white);text-transform:uppercase}
.about-text{position:absolute;left:561px;top:194px;width:527px;font-size:16px;line-height:28px;color:var(--white);text-align:justify}
.btn-outline{position:absolute;left:561px;top:308px;width:135px;height:46px;border:1px solid var(--white);border-radius:3px;color:var(--white);font-family:"Roboto",sans-serif;font-weight:500;font-size:15px;display:flex;align-items:center;justify-content:center}

/* locations */
.map-card{position:absolute;top:1957px;width:457px;height:426px;box-shadow:0 1px 4px rgba(0,0,0,.25);background:var(--white)}
.map-area{position:absolute;left:0;top:0;width:100%;height:309px}
.map-light{background:linear-gradient(135deg,#eef0f1,#dde2e4)}
.map-dark{background:linear-gradient(135deg,#3b4643,#2a302f)}
.map-caption{position:absolute;left:0;top:309px;width:100%;height:117px;padding:30px 70px 0 75px;font-size:16px;line-height:26px}
.map-caption svg{position:absolute;left:46px;top:34px}
.caption-active{background:var(--navy);color:var(--white)}
.caption-plain{color:var(--body)}
.divider-dots{position:absolute;left:598px;top:1957px;height:342px;border-left:1px dotted #aaa}

/* reviews */
.reviews-band{position:absolute;left:0;top:2480px;width:1200px;height:479px;background:var(--olive)}
.reviews-band .section-title{color:var(--white);top:70px}
.review-card{position:absolute;top:192px;width:311px;height:206px;background:var(--white);text-align:center}
.avatar{position:absolute;left:50%;top:-46px;margin-left:-40px;width:80px;height:80px;border-radius:50%;border:3px solid var(--white);background:linear-gradient(180deg,#9aa2ad,#5f6670)}
.review-card h4{position:absolute;top:53px;width:100%;font-family:"Roboto",sans-serif;font-weight:500;font-size:16px;color:var(--ink);text-transform:uppercase}
.stars{position:absolute;top:80px;width:100%;font-size:11px;letter-spacing:2px;color:var(--star)}
.review-card p{position:absolute;top:99px;width:100%;font-size:15px;line-height:27px;color:var(--body)}
.slider-arrow{position:absolute;top:272px}

/* blog */
.blog-photo{position:absolute;left:136px;top:3182px;width:340px;height:247px;background:linear-gradient(135deg,#3a4450,#7e6e62 55%,#d2682c 80%,#55606c)}
.blog-title{position:absolute;left:576px;top:3182px;width:520px;font-family:"Roboto",sans-serif;font-weight:500;font-size:20px;line-height:32px;color:var(--ink)}
.blog-date{position:absolute;left:576px;top:3260px;font-size:16px;color:var(--body);display:flex;align-items:center;gap:8px}
.blog-text{position:absolute;left:576px;top:3299px;width:515px;font-size:16px;line-height:33px;color:var(--body)}

/* footer */
.site-footer{position:absolute;left:0;top:3558px;width:1200px;height:294px;background:var(--footer);color:var(--white)}
.footer-brand{position:absolute;left:480px;top:53px;display:flex;align-items:center;gap:10px}
.footer-brand .brand-mark{width:42px;height:42px;background:var(--white)}
.footer-brand .brand-name{color:var(--white);font-size:12px;line-height:12px}
.footer-sep{position:absolute;left:640px;top:36px;height:72px;border-left:1px dotted #999}
.footer-badge{position:absolute;left:664px;top:40px;width:60px;height:64px;background:var(--white)}
.footer-links{position:absolute;left:0;top:143px;width:1200px;text-align:center;font-size:14px}
.footer-links span{margin:0 12px}
.socials{position:absolute;top:183px;left:436px;display:flex;gap:9px}
.socials span{width:34px;height:34px;border:1px solid #bbb;border-radius:50%}
.footer-mail{position:absolute;left:604px;top:192px;font-size:14px;display:flex;align-items:center;gap:8px}
.copyright{position:absolute;left:0;top:248px;width:1200px;text-align:center;font-size:13px}
</style>
</head>
<body>

<header class="site-header">
  <div class="brand">
    <span class="brand-mark"></span>
    <span class="brand-name">Meridian<br>Heart<br>Society</span>
  </div>
  <div class="phone">
    <span class="phone-icon">
      <svg width="16" height="16" viewBox="0 0 24 24"><path fill="#0b2e5e" d="M6.6 10.8a15 15 0 0 0 6.6 6.6l2.2-2.2c.3-.3.7-.4 1-.2 1.1.4 2.3.6 3.6.6.6 0 1 .4 1 1V20c0 .6-.4 1-1 1A17 17 0 0 1 3 4c0-.6.4-1 1-1h3.5c.6 0 1 .4 1 1 0 1.3.2 2.5.6 3.6.1.3 0 .7-.2 1z"/></svg>
    </span>
    <span class="phone-num">555 0142 300</span>
  </div>
  <div class="search">Search
    <svg width="13" height="13" viewBox="0 0 24 24"><circle cx="10" cy="10" r="7" fill="none" stroke="#555" stroke-width="2.5"/><path d="M15 15l6 6" stroke="#555" stroke-width="2.5"/></svg>
  </div>
  <nav class="main-nav">
    <a class="active" style="left:0">HOME</a>
    <a style="left:60px">ABOUT</a>
    <a style="left:124px">BLOG</a>
    <a style="left:181px">PRODUCT&amp; SERVICES</a>
    <a style="left:339px">SOLUTIONS</a>
    <a style="left:432px">RESOURCE</a>
    <a style="left:523px">CONTACT US</a>
  </nav>
</header>

<section class="hero" role="img" aria-label="Photo of a rescuer placing AED pads on the chest of a person lying on the ground">
  <h1 class="hero-title">BRINGING AEDs<br>IN NEW YORK ONLINE</h1>
  <p class="hero-text">Sed ut perspiciatis unde omnis iste natus error sit accusantium doloremque laudantium, totam rem aperiam</p>
  <a class="btn-quote">GET A QUOTE</a>
  <div class="hero-dots"><span></span><span class="on"></span><span></span></div>
</section>

<h2 class="section-title" style="top:812px">What We Do</h2>
<p class="section-lead" style="top:873px">At vero eos et accusamus et iusto odio dignissimos ducimus qui blanditiis praesentium<br>atque cupiditate non provident, similique sunt in culpa qui officia deserun</p>

<article class="service-card" style="left:112px">
  <div class="service-icon">
    <svg width="48" height="48" viewBox="0 0 48 48"><rect x="4" y="4" width="40" height="40" rx="5" fill="none" stroke="#222" stroke-width="2"/><path d="M8 26h9l4-9 5 16 4-10 2 3h8" fill="none" stroke="#222" stroke-width="2" stroke-linejoin="round"/></svg>
  </div>
  <h3>CARDIAC PULSATION</h3>
  <p>Nam libero tempore soluta<br>nobis est eligendi optio<br>cumque nihil impedit</p>
  <div class="read-more">Read More &nbsp;»</div>
</article>
<article class="service-card" style="left:358px">
  <div class="service-icon">
    <svg width="50" height="50" viewBox="0 0 50 50"><path d="M8 42L30 20M14 8l6 6-4 4-6-6a8 8 0 0 0 10 10l24 24" fill="none" stroke="#222" stroke-width="2.2" stroke-linecap="round"/><path d="M42 8l-26 26M36 6l8 8M10 38l2 2" fill="none" stroke="#222" stroke-width="2.2" stroke-linecap="round"/></svg>
  </div>
  <h3>ACCUSANTIUM</h3>
  <p>Nam libero tempore soluta<br>nobis est eligendi optio<br>cumque nihil impedit</p>
  <div class="read-more">Read More &nbsp;»</div>
</article>
<article class="service-card" style="left:604px">
  <div class="service-icon">
    <svg width="50" height="50" viewBox="0 0 50 50"><path d="M42 18A19 19 0 1 1 34 8" fill="none" stroke="#222" stroke-width="2"/><path d="M34 3v6h6" fill="none" stroke="#222" stroke-width="2"/><text x="25" y="32" text-anchor="middle" font-family="Roboto,sans-serif" font-size="18" fill="#222">24</text></svg>
  </div>
  <h3>FULL TIME STAFF</h3>
  <p>Nam libero tempore soluta<br>nobis est eligendi optio<br>cumque nihil impedit</p>
  <div class="read-more">Read More &nbsp;»</div>
</article>
<article class="service-card" style="left:850px">
  <div class="service-icon">
    <svg width="50" height="50" viewBox="0 0 50 50"><rect x="20" y="4" width="24" height="16" rx="3" fill="none" stroke="#222" stroke-width="2"/><circle cx="20" cy="24" r="7" fill="none" stroke="#222" stroke-width="2"/><path d="M6 44c0-8 6-12 14-12s14 4 14 12z" fill="none" stroke="#222" stroke-width="2"/></svg>
  </div>
  <h3>EXPERT ADVICE</h3>
  <p>Nam libero tempore soluta<br>nobis est eligendi optio<br>cumque nihil impedit</p>
  <div class="read-more">Read More &nbsp;»</div>
</article>

<section class="about-band">
  <div class="about-art" role="img" aria-label="Illustration of an orange AED unit beside a green defibrillator sign"></div>
  <h2 class="about-title">At vero eos et accusamus<br>et iusto odio</h2>
  <p class="about-text">Temporibus autem quibusdam &nbsp;officiis debitis necessitatibus saepe eveniet voluptates repudiandae molestiae non Itaque voluptatibus maiores alias consequatur aut perferendis.</p>
  <a class="btn-outline">ABOUT US</a>
</section>

<h2 class="section-title" style="top:1878px;left:-24px">Our Location</h2>

<div class="map-card" style="left:111px">
  <div class="map-area map-light" role="img" aria-label="Light street map of New York City with a red location pin"></div>
  <div class="map-caption caption-active">
    <svg width="12" height="16" viewBox="0 0 12 16"><path d="M6 0a6 6 0 0 0-6 6c0 4.5 6 10 6 10s6-5.5 6-10a6 6 0 0 0-6-6zm0 8.5A2.5 2.5 0 1 1 6 3.5a2.5 2.5 0 0 1 0 5z" fill="#fff"/></svg>
    Nor again is there anyone who loves or pursues or desires to obtain pain
  </div>
</div>
<div class="divider-dots"></div>
<div class="map-card" style="left:630px">
  <div class="map-area map-dark" role="img" aria-label="Dark-themed street map of New York City with a red location pin"></div>
  <div class="map-caption caption-plain">
    <svg width="12" height="16" viewBox="0 0 12 16"><path d="M6 0a6 6 0 0 0-6 6c0 4.5 6 10 6 10s6-5.5 6-10a6 6 0 0 0-6-6zm0 8.5A2.5 2.5 0 1 1 6 3.5a2.5 2.5 0 0 1 0 5z" fill="#777"/></svg>
    Nor again is there anyone who loves or pursues or desires to obtain pain
  </div>
</div>

<section class="reviews-band">
  <h2 class="section-title">Reviews</h2>
  <svg class="slider-arrow" style="left:46px" width="14" height="22" viewBox="0 0 14 22"><path d="M11 2L3 11l8 9" fill="none" stroke="#fff" stroke-width="2.5"/></svg>
  <svg class="slider-arrow" style="left:1143px" width="14" height="22" viewBox="0 0 14 22"><path d="M3 2l8 9-8 9" fill="none" stroke="#fff" stroke-width="2.5"/></svg>

  <article class="review-card" style="left:114px">
    <div class="avatar" role="img" aria-label="Portrait photo of the reviewer"></div>
    <h4>Ellis Varn</h4>
    <div class="stars">★★★★★</div>
    <p>Nam libero tempore, &nbsp;soluta nobis<br>est eligendi optio cumque nihil<br>impedit quo minus id</p>
  </article>
  <article class="review-card" style="left:446px">
    <div class="avatar" role="img" aria-label="Portrait photo of the reviewer"></div>
    <h4>Owen Hale</h4>
    <div class="stars">★★★★★</div>
    <p>Nam libero tempore, &nbsp;soluta nobis<br>est eligendi optio cumque nihil<br>impedit quo minus id</p>
  </article>
  <article class="review-card" style="left:778px">
    <div class="avatar" role="img" aria-label="Portrait photo of the reviewer"></div>
    <h4>Marcus Reed</h4>
    <div class="stars">★★★★★</div>
    <p>Nam libero tempore, &nbsp;soluta nobis<br>est eligendi optio cumque nihil<br>impedit quo minus id</p>
  </article>
</section>

<h2 class="section-title" style="top:3045px">Latest Blog</h2>

<div class="abs" style="left:111px;top:3158px;width:137px;height:103px;background:var(--navy)"></div>
<div class="abs" style="left:365px;top:3339px;width:138px;height:118px;background:var(--navy)"></div>
<div class="blog-photo" role="img" aria-label="Photo of paramedics loading a stretcher into an ambulance"></div>
<h3 class="blog-title">On the other hand, we denounce with righteous &nbsp;charms indignation and dislike men who are so</h3>
<div class="blog-date">
  <svg width="15" height="15" viewBox="0 0 16 16"><rect x="1" y="3" width="14" height="12" rx="1" fill="none" stroke="#0b2e5e" stroke-width="1.5"/><path d="M1 7h14M5 1v4M11 1v4" stroke="#0b2e5e" stroke-width="1.5"/></svg>
  March 28, 2019
</div>
<p class="blog-text">Sed &nbsp;ut &nbsp;perspiciatis unde &nbsp;omnis iste &nbsp;sit voluptatem accusantium doloremque laudantium, totam rem aperiam, eaque ipsa quae ab illo inventore veritatis et quasi nesciunt.</p>

<footer class="site-footer">
  <div class="footer-brand">
    <span class="brand-mark"></span>
    <span class="brand-name">Meridian<br>Heart<br>Society</span>
  </div>
  <div class="footer-sep"></div>
  <div class="footer-badge"></div>
  <div class="footer-links"><span>Home</span>|<span>About</span>|<span>Blog</span>|<span>Product&amp; services</span>|<span>Solutions</span>|<span>Contact Us</span></div>
  <div class="socials"><span aria-label="Social profile"></span><span aria-label="Social profile"></span><span aria-label="Social profile"></span></div>
  <div class="footer-mail">
    <svg width="14" height="11" viewBox="0 0 14 11"><rect x=".75" y=".75" width="12.5" height="9.5" fill="none" stroke="#fff" stroke-width="1.3"/><path d="M1 1l6 5 6-5" fill="none" stroke="#fff" stroke-width="1.3"/></svg>
    info@harborlanedevices.org
  </div>
  <div class="copyright">© 2019 Harborlane Devices.All Rights Reserved</div>
</footer>

</body>
</html>
```